Child sleep consultant needs a flyer to attract new clients

We need a flyer that will attract the attention of parents with children between newborn and 3 years old who may be experiencing sleep issues. The flyer will be placed at places such as community centres, doctors room, play centres, etc.

Our business is called Drowsy Tiny Folk and provides a sleep consultancy service. Our service essentially provides a routine for parents to follow and general advice. Our service is not medical advice.

We need the flyer to have an overall tone that is soft and peaceful however can catch the attention of parents who may be struggling on minimal sleep. We would like photos with minimal text. The colour we use is green.

We will provide the text to appear in the flyer once we have a better idea of the layout that we prefer for the flyer. The text however wont be extensive, just some catchy points.

We want to direct people to our website which is drowsytinyfolk.com.au. We also have a facebook page, which is Drowsy Tiny Folk.

We have a logo that we would like to appear on the flyer. We will attach the file once the uploader on pixel bazaar is fixed.

Our consultant is a certified Rest Wise consultant, which has a separate logo that should appear somewhere on the logo. I will attach this once the uploader is fixed.

When we print the flyer - we want to print A5 SIZE ... please make sure the formatting is OK for this size.

Target Market(s)

Mums and Dads with children between newborn and 3 years old.

Industry/Entity Type

Consultant

Colors
cadf82

Requirements
Must have
• - Our logo.
• - Rest Wise consultant logo - both attached to this brief.
• - Contact details - including phone number, email address and website
• - MUST be suitable for A5 printable size, double sided please.
• Must have the following text:
• If your baby or toddler isn't sleeping through the night, neither are you - and this means you are probably feeling physically and mentally exhausted, stressed, depressed and irritable, afraid you might be damaging your child and disconnected from your partner.
• The good news is nearly all healthy children 3 months or older are physically capable of sleeping 12 solid hours without waking. They just need to be taught the healthy sleep habits that enable them to do so.
• I can help with the sleep issues your child is experiencing. As a certified Rest Wise (insert trademark TM here) I can help if:
• - your child will only fall asleep when nursing or bottle feeding
• - your child needs a dummy in order fall asleep
• - you're waking up with your child one or more times per night
• - your child needs to be rocked, patted, or taken for a car ride to go to sleep
• - your own lack of sleep is starting to take a toll on your family
• I've been personally trained by Mara Felgate, best selling author of the Rest Wise (insert trade mark symbol here) Program to teach her sleep training methods to families like yours. Mara's methods have already helped over 30,000 parents and children and I'd be delighted to help your family next!
• Call or email for a free 15 minute consultation
• I would love to connect with you to talk about your child's specific situation and discuss different solutions.

```html
<!DOCTYPE html>
<html lang="en">
<head>
<meta charset="utf-8">
<title>Drowsy Tiny Folk – A5 Flyer</title>
<link href="https://fonts.googleapis.com/css2?family=Pathway+Gothic+One&display=swap" rel="stylesheet">
<style>
  :root{
    --bg:#e9e9ea;
    --paper:#ffffff;
    --green:#84b077;
    --green-dark:#5f9a57;
    --green-text:#6aa362;
    --lime:#cadf82;
    --lime-soft:#dbe9b8;
    --ink:#4d4d4d;
    --white:#ffffff;
  }
  *{box-sizing:border-box;margin:0;padding:0}
  html,body{width:1200px;height:960px;overflow:hidden}
  body{background:var(--bg);font-family:"Pathway Gothic One",sans-serif;color:var(--ink);position:relative}
  .page{position:absolute;top:112px;width:517px;height:736px;background:var(--paper);overflow:hidden}
  .page--front{left:58px}
  .page--back{left:623px}
  .abs{position:absolute}
  svg.fill{position:absolute;left:0;top:0}

  /* front */
  .brand{position:absolute;display:flex;align-items:center;gap:10px;color:var(--green-text);font-size:31px;line-height:0.95}
  .brand__dot{width:52px;height:52px;border-radius:50%;background:var(--lime);flex:none}
  .front .brand{left:25px;top:48px}
  .headline{left:280px;top:38px;width:220px;color:var(--green-dark);font-size:29px;line-height:33px}
  .headline span{display:block}
  .cta{left:43px;top:376px;width:216px;height:136px}
  .cta__text{position:absolute;left:0;top:38px;width:216px;color:var(--white);font-size:22px;line-height:25px;text-align:center;letter-spacing:.3px}
  .intro{left:38px;top:524px;width:441px;font-size:12.4px;line-height:18.5px;text-align:center;color:var(--ink)}
  .tagline{left:0;top:634px;width:517px;text-align:center;color:var(--green-text);font-size:26px;letter-spacing:.3px;opacity:.85}
  .contact-line{left:0;top:676px;width:517px;text-align:center;color:var(--green-text);font-size:22px}
  .star-sep{color:var(--lime);margin:0 6px}

  /* back */
  .back-head{left:0;top:46px;width:516px;text-align:center;color:var(--white);font-size:21px;line-height:29px;letter-spacing:.2px}
  .reasons{left:26px;top:116px;width:470px;display:flex;justify-content:space-between;list-style:none}
  .reasons li{width:90px;text-align:center;color:var(--white);font-size:14px;line-height:21px}
  .reasons li::before{content:"★";display:block;color:var(--lime);font-size:18px;line-height:20px;margin-bottom:4px}
  .trained{left:20px;top:312px;width:476px;text-align:center;color:var(--white);font-size:14.5px;line-height:22px}
  .results{left:246px;top:376px;width:246px;text-align:center;color:var(--white);font-size:18px;line-height:22.5px}
  .connect{left:20px;top:506px;width:476px;text-align:center;color:var(--ink);font-size:22px;line-height:29px}
  .back .brand{left:41px;top:606px}
  .ribbon{left:241px;top:582px;width:248px;height:36px}
  .ribbon__text{position:absolute;left:0;top:7px;width:248px;text-align:center;color:var(--ink);font-size:17px}
  .details{left:262px;top:628px;width:200px;text-align:center;color:var(--ink)}
  .details p{font-size:16px;line-height:26px}
  .details .phone{font-size:19px}
  .social{display:inline-flex;align-items:center;gap:6px}
  .social__sq{width:15px;height:15px;background:var(--green);display:inline-block}
</style>
</head>
<body>

<!-- Front side -->
<section class="page page--front front">
  <svg class="fill" width="517" height="736" viewBox="0 0 517 736" role="img" aria-label="Photograph of a sleeping mother and father in bed with their newborn baby">
    <defs>
      <linearGradient id="photoTone" x1="0" y1="0" x2="1" y2="1">
        <stop offset="0" stop-color="#efe9e6"/>
        <stop offset=".5" stop-color="#d9c4b6"/>
        <stop offset="1" stop-color="#e8dcd5"/>
      </linearGradient>
    </defs>
    <path d="M0,200 C40,170 90,175 120,200 C150,160 230,150 260,185 C300,170 330,190 350,190 C420,180 480,190 517,170 L517,450 C470,470 420,490 360,495 C300,500 250,490 230,480 L0,470 Z" fill="url(#photoTone)"/>
  </svg>

  <div class="brand"><span class="brand__dot"></span><span>Drowsy<br>Tiny<br>Folk</span></div>

  <h1 class="abs headline">
    <span>We help families</span>
    <span style="padding-left:30px">and their little ones</span>
    <span>to get the sleep</span>
    <span style="padding-left:74px">they need.</span>
  </h1>

  <div class="abs cta">
    <svg class="fill" width="216" height="136" viewBox="0 0 216 136">
      <path d="M20,136 C4,136 0,118 0,104 C0,80 14,66 34,64 C38,34 62,14 94,16 C118,4 160,6 176,34 C200,40 212,58 212,80 C216,112 206,136 186,136 Z" fill="var(--green)" stroke="var(--lime-soft)" stroke-width="2"/>
      <text x="80" y="38" fill="var(--lime)" font-size="18">★</text>
      <text x="98" y="46" fill="var(--lime)" font-size="11">★</text>
    </svg>
    <p class="cta__text">CALL OR EMAIL FOR<br><span style="padding-left:40px">A FREE 15 MINUTE</span><br>CONSULTATION <span style="color:var(--lime);font-size:14px">★</span></p>
  </div>

  <p class="abs intro">If your baby or toddler isn't sleeping through the night, neither are you - and this means you are probably feeling physically and mentally exhausted, stressed, depressed and irritable, afraid you might be damaging your child and disconnected from your partner. The good news is nearly all healthy children 3 months or older are physically capable of sleeping 12 solid hours without waking. They just need to be taught the healthy sleep habits that enable them to do so.</p>

  <p class="abs tagline">YOUR LITTLE PERSON IS NEVER TOO YOUNG TO START</p>
  <p class="abs contact-line">E: nina@drowsytinyfolk.com.au <span class="star-sep">★</span> P: 0400 555 017</p>
</section>

<!-- Back side -->
<section class="page page--back back">
  <svg class="fill" width="516" height="733" viewBox="0 0 516 733">
    <path d="M0,0 L516,0 L516,490 C480,500 440,505 400,490 C380,510 330,515 300,495 C280,505 250,495 240,480 C210,440 180,410 150,410 C120,380 60,400 45,400 C20,380 25,330 30,300 C15,300 5,300 0,296 Z" fill="var(--green)"/>
    <g fill="none" stroke="var(--white)" stroke-width="1.3" stroke-dasharray="5 4">
      <path d="M0,226 C60,240 110,260 150,265 C200,275 250,285 290,285 C350,285 400,270 450,265 C480,265 500,280 516,308"/>
      <circle cx="122" cy="278" r="16"/>
      <circle cx="290" cy="272" r="9"/>
    </g>
    <!-- certification badge -->
    <path d="M14,470 C2,470 0,450 6,438 C2,418 18,406 34,410 C44,390 72,384 92,396 C108,384 136,392 140,414 C160,418 170,438 162,454 C164,470 150,472 140,472 Z" fill="var(--white)" stroke="var(--lime)" stroke-width="1.5"/>
    <!-- small stars and heart -->
    <text x="180" y="482" fill="var(--lime)" font-size="24">★</text>
    <text x="209" y="490" fill="var(--lime)" font-size="13">★</text>
    <path d="M218,460 C204,452 206,440 214,440 C218,440 220,443 221,445 C222,443 226,440 230,441 C238,443 236,455 218,460 Z" fill="var(--lime)"/>
    <text x="444" y="574" fill="var(--lime)" font-size="13">★</text>
  </svg>

  <h2 class="abs back-head">I CAN HELP WITH THE SLEEP ISSUES YOUR CHILD IS EXPERIENCING.<br>AS A CERTIFIED REST WISE™ I CAN HELP IF:</h2>

  <ul class="abs reasons">
    <li>your child will only fall asleep when nursing or bottle feeding</li>
    <li>your child needs a dummy in order fall asleep</li>
    <li>you're waking up with your child one or more times per night</li>
    <li>your child needs to be rocked, patted, or taken for a car ride to go to sleep</li>
    <li>your own lack of sleep is starting to take a toll on your family</li>
  </ul>

  <p class="abs trained">I've been personally trained by Mara Felgate, best selling author of<br>the Rest Wise™ Program to teach her sleep training methods to families like yours.</p>

  <p class="abs results">MARA'S METHODS HAVE ALREADY HELPED OVER 30,000 PARENTS AND CHILDREN AND I'D BE DELIGHTED TO HELP YOUR FAMILY NEXT!</p>

  <p class="abs connect">I would love to connect with you to talk about your child's<br>specific situation and discuss different solutions.</p>

  <div class="brand"><span class="brand__dot"></span><span>Drowsy<br>Tiny<br>Folk</span></div>

  <div class="abs ribbon">
    <svg class="fill" width="248" height="36" viewBox="0 0 248 36">
      <path d="M0,2 L248,6 L238,20 L248,34 L6,32 L14,17 Z" fill="var(--lime-soft)"/>
    </svg>
    <p class="ribbon__text">www.drowsytinyfolk.com.au</p>
  </div>

  <div class="abs details">
    <p>E: nina@drowsytinyfolk.com.au</p>
    <p class="phone">P: 0400 555 017</p>
    <p><span class="social"><span class="social__sq"></span>drowsytinyfolk</span></p>
  </div>
</section>

</body>
</html>
```